Redesign Local Plumber Website

redesign of existing plumbing website

Mobile Responsive
Professional
modern
easy enquiry
Map embed

Please see existing site for text and images. Please feel free to suggest improvements and any additional features
callthepipeteam.com.au

attached is logo and the Australian owned badge which we also want featuring

Target Market(s)

Plumbing & Gas Services

Industry/Entity Type

Plumbing

Font styles to use
Sans Serif

Requirements
Must have
• existing logo
Nice to have
• new design
Should not have
• same design

```html
<!DOCTYPE html>
<html lang="en">
<head>
<meta charset="utf-8">
<title>Call The Pipe Team – Plumbing &amp; Gas</title>
<link href="https://fonts.googleapis.com/css2?family=Poppins:wght@300;400;500;600;700&display=swap" rel="stylesheet">
<style>
:root{
  --blue:#2f7cf6;
  --orange:#f7931e;
  --navy:#1e2d52;
  --footer:#253a63;
  --text:#666;
  --light:#999;
  --band:#f9f7f8;
  --white:#fff;
}
*{box-sizing:border-box;margin:0;padding:0}
html,body{width:1200px;height:4823px;overflow:hidden}
body{font-family:'Poppins',sans-serif;color:var(--text);background:var(--white);position:relative}
.abs{position:absolute}
.btn{position:absolute;background:var(--orange);color:var(--white);font-size:13px;font-weight:500;display:flex;align-items:center;justify-content:center;text-transform:uppercase;letter-spacing:.3px}
.ph{position:absolute}

/* header */
.logo{left:92px;top:30px;display:flex;align-items:center;gap:14px}
.logo-dot{width:54px;height:54px;border-radius:50%;background:var(--blue)}
.logo-name{font-size:30px;font-weight:700;color:var(--navy);letter-spacing:.5px}
.nav{left:487px;top:70px;font-size:13px;color:#333;letter-spacing:.6px}
.nav a{color:#333;text-decoration:none;position:absolute;white-space:nowrap}
.nav a.active{color:var(--blue)}
.nav-wave{left:487px;top:92px}
.top-social{left:869px;top:0;width:51px;height:47px;font-size:10px;text-transform:none}
.top-phone{left:942px;top:0;width:178px;height:47px;gap:8px;font-size:14px;letter-spacing:1px}

/* hero */
.hero{left:0;top:118px;width:1200px;height:642px;background:linear-gradient(120deg,#8a8f93 0%,#c9c2b4 35%,#6d6f72 60%,#3f4246 100%)}
.hero-shade{left:0;top:118px;width:1200px;height:642px;background:rgba(20,25,35,.35)}
.hero-title{left:0;top:318px;width:1200px;text-align:center;color:var(--white);font-size:47px;font-weight:700;letter-spacing:.5px}
.hero-sub{left:250px;top:394px;width:700px;text-align:center;color:var(--white);font-size:15px;line-height:26px}
.hero-btn{left:510px;top:455px;width:180px;height:48px}

/* estimate */
.estimate{left:154px;top:676px;width:892px;height:169px;background:var(--blue);box-shadow:0 10px 30px rgba(0,0,0,.15)}
.estimate h3{position:absolute;left:22px;top:38px;color:var(--white);font-size:19px;font-weight:600}
.field{position:absolute;top:87px;height:47px;background:var(--white);font-size:12px;color:#aaa;padding-left:14px;display:flex;align-items:center;border-radius:2px}
.estimate .btn{top:87px;height:47px;left:678px;width:190px;font-size:14px;font-weight:600}

/* about */
.h2{position:absolute;color:var(--navy);font-weight:600;font-size:36px}
.about-img1{left:111px;top:993px;width:291px;height:347px;background:linear-gradient(150deg,#d9d6d2,#a59a8f 60%,#6f7a86);border-radius:4px}
.about-img2{left:272px;top:1130px;width:260px;height:348px;background:linear-gradient(160deg,#c9c9cb,#8e9196 55%,#54585e);border-radius:4px}
.play{left:232px;top:1211px;width:88px;height:88px;border-radius:50%;background:var(--white);display:flex;align-items:center;justify-content:center}
.about-text{left:550px;top:980px;width:538px;font-size:13.5px;line-height:25.5px;text-align:justify}
.ticks{left:550px;top:1124px;width:540px;list-style:none;font-size:13.5px;line-height:25px}
.ticks li{position:relative;padding-left:26px;margin-bottom:12px}
.ticks svg{position:absolute;left:3px;top:8px}
.about-btn{left:555px;top:1448px;width:190px;height:47px}

/* gas & plumbing band */
.band{left:0;top:1585px;width:1200px;height:702px;background:var(--band)}
.band-text{left:112px;top:1746px;width:976px;text-align:center;font-size:14px;line-height:25.5px;color:#777}
.band-text p{margin-bottom:26px}

/* services */
.svc-sub{left:180px;top:2413px;width:840px;text-align:center;font-size:17px;line-height:26px;color:#444}
.h3{position:absolute;color:var(--blue);font-size:24px;font-weight:500}
.svc-text{font-size:14px;line-height:25px;color:#555}
.check{position:absolute;font-size:14px;color:#555;line-height:22px}
.check svg{position:absolute;left:-22px;top:4px}
.readmore{position:absolute;color:var(--orange);font-size:13px;text-decoration:underline;text-transform:uppercase}
.plumb-back{left:803px;top:2530px;width:357px;height:250px;background:linear-gradient(140deg,#bcc2c7,#7e8b99 60%,#4a5866)}
.plumb-frame{left:660px;top:2597px;width:358px;height:353px;border:11px solid var(--blue)}
.plumb-front{left:640px;top:2622px;width:360px;height:351px;background:linear-gradient(160deg,#c8ced4,#3c6fb6 55%,#273a5a)}
.gas-frame{left:140px;top:3135px;width:360px;height:353px;border:11px solid var(--orange)}
.gas-photo{left:185px;top:3108px;width:358px;height:352px;background:linear-gradient(120deg,#6d7a86,#a9b0b7 45%,#d9a62e 60%,#7c8691)}
.bullets{left:610px;top:3180px;width:450px;list-style:none;font-size:14px;line-height:24px;color:#555}
.bullets li{position:relative;padding-left:13px;margin-bottom:22px}
.bullets li::before{content:"";position:absolute;left:0;top:11px;width:3px;height:3px;background:#555;border-radius:50%}

/* cards */
.card{position:absolute;top:3580px;height:442px;background:var(--white);box-shadow:0 4px 18px rgba(0,0,0,.12);text-align:center}
.card-photo{height:247px;width:100%}
.card h4{color:var(--blue);font-size:20px;font-weight:500;margin-top:52px}
.card p{font-size:13px;line-height:23px;color:#666;margin:18px auto 0;width:262px}
.pay-card{position:absolute;top:3865px;width:52px;height:32px;border-radius:3px}

/* partners */
.partner{position:absolute;top:4230px;height:80px;width:220px;background:var(--white);box-shadow:0 3px 14px rgba(0,0,0,.12);display:flex;align-items:center;justify-content:center}
.partner span{display:block;width:150px;height:34px;border-radius:17px}

/* footer */
.footer{left:0;top:4405px;width:1200px;height:418px;background:var(--footer)}
.badge{left:75px;top:4447px;width:80px;height:80px;border-radius:50%;background:#2f8a4a;border:4px solid var(--white)}
.foot-about{left:68px;top:4533px;width:202px;font-size:14px;line-height:25px;text-align:justify;color:var(--white)}
.foot-h{position:absolute;top:4462px;font-size:16px;font-weight:600;text-transform:uppercase;color:var(--white)}
.foot-h::after{content:"";position:absolute;left:0;bottom:-8px;width:60px;height:2px;background:var(--white)}
.quick{left:340px;top:4516px;list-style:none;font-size:12.5px;line-height:25.5px;color:var(--white)}
.contact{left:538px;top:4516px;list-style:none;font-size:12.5px;line-height:21px;color:var(--white)}
.contact li{position:relative;padding-left:34px;margin-bottom:13px}
.contact svg{position:absolute;left:0;top:3px}
.map{left:866px;top:4456px;width:246px;height:206px;background:linear-gradient(135deg,#eef0ea,#dfe6dc);border-radius:3px}
.foot-line{left:0;top:4748px;width:1200px;height:1px;background:rgba(255,255,255,.25)}
.copy{left:0;top:4772px;width:1200px;text-align:center;font-size:12px;color:var(--white)}
</style>
</head>
<body>

<!-- header -->
<div class="abs logo"><span class="logo-dot"></span><span class="logo-name">Call The Pipe Team</span></div>
<nav class="abs nav">
  <a class="active" style="left:0;top:0">Home</a>
  <a style="left:88px;top:0">About Us</a>
  <a style="left:201px;top:0">Services</a>
  <a style="left:311px;top:0">Septics</a>
  <a style="left:413px;top:0">Products</a>
  <a style="left:527px;top:0">Contact Us</a>
</nav>
<svg class="abs nav-wave" width="44" height="8" viewBox="0 0 44 8"><path d="M2 4 Q8 0 14 4 T26 4 T38 4 T44 4" fill="none" stroke="#2f7cf6" stroke-width="1.6"/></svg>
<div class="btn top-social">Follow</div>
<div class="btn top-phone">
  <svg width="13" height="13" viewBox="0 0 24 24"><path fill="#fff" d="M6.6 10.8a15 15 0 0 0 6.6 6.6l2.2-2.2c.3-.3.7-.4 1-.2 1.1.4 2.3.6 3.6.6.6 0 1 .4 1 1V20c0 .6-.4 1-1 1A17 17 0 0 1 3 4c0-.6.4-1 1-1h3.5c.6 0 1 .4 1 1 0 1.3.2 2.5.6 3.6.1.3 0 .7-.2 1z"/></svg>
  1800 472 918
</div>

<!-- hero -->
<div class="ph hero" role="img" aria-label="Plumber in a hard hat working on wall pipes and valves"></div>
<div class="abs hero-shade"></div>
<h1 class="abs hero-title">CALL THE PIPE TEAM</h1>
<p class="abs hero-sub">Consectetur adipiscing elit, sed do eiusmod tempor incididunt ut labore et dolore magna aliqua. Ut enim ad minim veniam quis</p>
<div class="btn hero-btn">Get Started</div>

<!-- estimate -->
<form class="abs estimate">
  <h3>REQUEST AN ESTIMATE</h3>
  <div class="field" style="left:22px;width:190px">Name*</div>
  <div class="field" style="left:242px;width:189px">Email*</div>
  <div class="field" style="left:460px;width:190px;justify-content:space-between;padding-right:12px">Select Services
    <svg width="9" height="6" viewBox="0 0 9 6"><path d="M1 1l3.5 3.5L8 1" fill="none" stroke="#999" stroke-width="1.3"/></svg></div>
  <div class="btn">Submit Now</div>
</form>

<!-- about -->
<h2 class="h2" style="left:550px;top:920px">ABOUT US</h2>
<div class="ph about-img1" role="img" aria-label="Plumber fixing pipes under a sink"></div>
<div class="ph about-img2" role="img" aria-label="Plumber kneeling beside a toilet with tools on the floor"></div>
<div class="abs play"><svg width="20" height="22" viewBox="0 0 20 22"><path d="M2 1l17 10L2 21z" fill="#222"/></svg></div>
<p class="abs about-text">Daniel has been in the plumbing and gas industry since high school, his father Ray was a plumber and estimator. Daniel has trained with reputable plumbers of his time and achieved apprentice of the year 2 years running, then taking out the "Apprentice of the Year" award for all trades during his apprenticeship.</p>
<ul class="abs ticks">
  <li><svg width="12" height="10" viewBox="0 0 12 10"><path d="M1 5l3.5 3.5L11 1" fill="none" stroke="#2f7cf6" stroke-width="2"/></svg>We provide a complete range of products services to suite our clients.</li>
  <li><svg width="12" height="10" viewBox="0 0 12 10"><path d="M1 5l3.5 3.5L11 1" fill="none" stroke="#2f7cf6" stroke-width="2"/></svg>Showroom – complete range of tap ware, sinks, bath and shower sets, toilets and showers – this is open by appointment</li>
  <li><svg width="12" height="10" viewBox="0 0 12 10"><path d="M1 5l3.5 3.5L11 1" fill="none" stroke="#2f7cf6" stroke-width="2"/></svg>Supply and install ATUs – Cascade 0-3 Alternative Treatment Unit Specialists</li>
  <li><svg width="12" height="10" viewBox="0 0 12 10"><path d="M1 5l3.5 3.5L11 1" fill="none" stroke="#2f7cf6" stroke-width="2"/></svg>New Housing and Renovations</li>
  <li><svg width="12" height="10" viewBox="0 0 12 10"><path d="M1 5l3.5 3.5L11 1" fill="none" stroke="#2f7cf6" stroke-width="2"/></svg>Hot Water Units – gas and/or a selection of solar options</li>
  <li><svg width="12" height="10" viewBox="0 0 12 10"><path d="M1 5l3.5 3.5L11 1" fill="none" stroke="#2f7cf6" stroke-width="2"/></svg>All Gas installations including BBQ's, Bayonets and Kitchen connections</li>
  <li><svg width="12" height="10" viewBox="0 0 12 10"><path d="M1 5l3.5 3.5L11 1" fill="none" stroke="#2f7cf6" stroke-width="2"/></svg>We carry a wide range of pumps, pressure vessels and parts.</li>
</ul>
<div class="btn about-btn">Read More</div>

<!-- plumbing & gas services band -->
<section class="abs band"></section>
<h2 class="h2" style="left:0;top:1658px;width:1200px;text-align:center">PLUMBING &amp; GAS SERVICES</h2>
<div class="abs band-text">
  <p>Call The Pipe Team is a family run business based in Brookvale since 2004, we service Midland to Wannamal, Ellenbrook to Brigadoon, Joondalup and Wanneroo to Bullsbrook, Toodyay to Gingin , Chittering and surrounding areas of Bullsbrook, Brigadoon, Ellenbrook, Averley, Henley Brook, Millendon, Gingin, Bindoon, Wannamal, Chittering, Midland, Upper Swan, Belhus, Wanneroo, Wangara, Malaga and The Vines.</p>
  <p>All of our plumbing and gas services are fully licensed, always on the go with vans that are well stocked for any plumbing situations. We offer a complete honest and reliable service, no call out fee, free quotes and professional advice. We believe in a duty of care to our customers.</p>
  <p>At Call The Pipe Team no job is too big or too small regardless if it's a complete bathroom, kitchen, laundry make over, new build or renovation. We are suppliers of quality tap ware and fixtures, agents for solar hot water and quality gas systems at an affordable price.</p>
  <p>Market leaders in installation of Alternative Treatment Units – Cascade, when only the best will do in nutrient retentive treatment products.</p>
  <p>We have a wide range of products to suite any budget, the have the experience to get the job done and we come to you.</p>
</div>

<!-- services -->
<h2 class="h2" style="left:0;top:2352px;width:1200px;text-align:center;font-weight:500">SERVICES</h2>
<p class="abs svc-sub">At Call The Pipe Team we have a whole series of goods solutions specially designed for our clients.</p>

<h3 class="h3" style="left:108px;top:2517px">PLUMBING</h3>
<div class="abs svc-text" style="left:110px;top:2580px;width:470px">Set-up all pipework for new housing or renovations including compliance paperwork.</div>
<div class="abs svc-text" style="left:110px;top:2644px">Installation of tap ware and fixtures:</div>
<div class="check" style="left:155px;top:2700px"><svg width="14" height="14" viewBox="0 0 14 14"><rect x=".5" y=".5" width="13" height="13" fill="#fff" stroke="#2f7cf6"/><path d="M3 7l3 3 5-6" fill="none" stroke="#2f7cf6" stroke-width="1.6"/></svg>Taps</div>
<div class="check" style="left:282px;top:2700px"><svg width="14" height="14" viewBox="0 0 14 14"><rect x=".5" y=".5" width="13" height="13" fill="#fff" stroke="#2f7cf6"/><path d="M3 7l3 3 5-6" fill="none" stroke="#2f7cf6" stroke-width="1.6"/></svg>Sinks</div>
<div class="check" style="left:424px;top:2700px"><svg width="14" height="14" viewBox="0 0 14 14"><rect x=".5" y=".5" width="13" height="13" fill="#fff" stroke="#2f7cf6"/><path d="M3 7l3 3 5-6" fill="none" stroke="#2f7cf6" stroke-width="1.6"/></svg>Toilets</div>
<div class="check" style="left:155px;top:2754px"><svg width="14" height="14" viewBox="0 0 14 14"><rect x=".5" y=".5" width="13" height="13" fill="#fff" stroke="#2f7cf6"/><path d="M3 7l3 3 5-6" fill="none" stroke="#2f7cf6" stroke-width="1.6"/></svg>Baths</div>
<div class="check" style="left:282px;top:2754px"><svg width="14" height="14" viewBox="0 0 14 14"><rect x=".5" y=".5" width="13" height="13" fill="#fff" stroke="#2f7cf6"/><path d="M3 7l3 3 5-6" fill="none" stroke="#2f7cf6" stroke-width="1.6"/></svg>Showers</div>
<div class="check" style="left:424px;top:2754px;width:200px"><svg width="14" height="14" viewBox="0 0 14 14"><rect x=".5" y=".5" width="13" height="13" fill="#fff" stroke="#2f7cf6"/><path d="M3 7l3 3 5-6" fill="none" stroke="#2f7cf6" stroke-width="1.6"/></svg>Installation of dishwashers and washing machines</div>
<div class="abs svc-text" style="left:110px;top:2820px;width:380px">We even install mirrors, towel rails and toilet roll holders<br>See our products page or in van catalogue</div>
<a class="readmore" style="left:111px;top:2924px">Read More</a>

<div class="ph plumb-back" role="img" aria-label="Plumber working under a kitchen sink"></div>
<div class="abs plumb-frame"></div>
<div class="ph plumb-front" role="img" aria-label="Plumber in blue uniform repairing a sink drain with wrenches"></div>

<div class="abs gas-frame"></div>
<div class="ph gas-photo" role="img" aria-label="Yellow gas valve handle on a wall pipe"></div>
<h3 class="h3" style="left:609px;top:3105px">GAS</h3>
<ul class="abs bullets">
  <li>All gas pipework installations to kitchen, heaters, BBQ's and Hot water Units</li>
  <li>Supply and install gas Hot Water Units</li>
  <li>Leak detection, gas line installation and repairs</li>
  <li>Gas appliance installation</li>
</ul>
<a class="readmore" style="left:610px;top:3417px">Read More</a>

<!-- cards -->
<div class="card" style="left:94px;width:312px">
  <div class="card-photo" role="img" aria-label="Smiling plumber holding a pipe wrench" style="background:linear-gradient(150deg,#4e86d6,#2a5fb0 60%,#1d3f7a)"></div>
  <h4>QUICK RESPONSE</h4>
  <p>If you've had enough of tradespeople who never turn up when they say they will, call Daniel at Call The Pipe Team.</p>
</div>
<div class="card" style="left:442px;width:316px">
  <h4 style="margin-top:78px">PAYMENT OPTIONS</h4>
  <p style="margin-top:16px;font-size:13.5px;line-height:25px">Electronic Transfer, all major credit cards accepted, Debit Cards and EFTPOS facilities, Credit account to approved clients only, All accounts are COD unless by prior arrangement</p>
</div>
<div class="pay-card" style="left:510px;background:#1b3f8f"></div>
<div class="pay-card" style="left:628px;background:#c8362c"></div>
<div class="btn" style="left:505px;top:3942px;width:188px;height:44px">Read More</div>
<div class="card" style="left:792px;width:314px">
  <div class="card-photo" role="img" aria-label="Hands fitting a chrome mixer tap with a wrench" style="background:linear-gradient(140deg,#c9ccd0,#8a9098 55%,#4d545c)"></div>
  <h4>VIEW OUR SHOWROOM</h4>
  <p>We handle all plumbing and gas installation including domestic and commercial</p>
</div>

<!-- partners -->
<h2 class="h2" style="left:0;top:4137px;width:1200px;text-align:center;font-weight:500">OUR PARTNERS</h2>
<div class="partner" style="left:109px"><span style="background:#f3a64a"></span></div>
<div class="partner" style="left:363px"><span style="background:#2e5fb8"></span></div>
<div class="partner" style="left:617px"><span style="background:#e8742a"></span></div>
<div class="partner" style="left:871px"><span style="background:#314a78"></span></div>

<!-- footer -->
<footer class="abs footer"></footer>
<div class="abs badge"></div>
<p class="abs foot-about">Daniel has been in the plumbing and gas industry since high school, his father Ray was a plumber and estimator.</p>
<h5 class="foot-h" style="left:340px">Quick Links</h5>
<ul class="abs quick">
  <li>Home</li><li>About Us</li><li>Services</li><li>Septics</li><li>Products</li><li>Contact Us</li>
</ul>
<h5 class="foot-h" style="left:538px">Contact Us</h5>
<ul class="abs contact">
  <li><svg width="13" height="13" viewBox="0 0 24 24"><path fill="#fff" d="M6.6 10.8a15 15 0 0 0 6.6 6.6l2.2-2.2c.3-.3.7-.4 1-.2 1.1.4 2.3.6 3.6.6.6 0 1 .4 1 1V20c0 .6-.4 1-1 1A17 17 0 0 1 3 4c0-.6.4-1 1-1h3.5c.6 0 1 .4 1 1 0 1.3.2 2.5.6 3.6.1.3 0 .7-.2 1z"/></svg>Free Call 1800 472 918</li>
  <li><svg width="13" height="13" viewBox="0 0 24 24"><path fill="#fff" d="M6.6 10.8a15 15 0 0 0 6.6 6.6l2.2-2.2c.3-.3.7-.4 1-.2 1.1.4 2.3.6 3.6.6.6 0 1 .4 1 1V20c0 .6-.4 1-1 1A17 17 0 0 1 3 4c0-.6.4-1 1-1h3.5c.6 0 1 .4 1 1 0 1.3.2 2.5.6 3.6.1.3 0 .7-.2 1z"/></svg>Daniel: 0412 305 781</li>
  <li><svg width="12" height="15" viewBox="0 0 12 15"><path fill="#fff" d="M6 0a6 6 0 0 0-6 6c0 4.5 6 9 6 9s6-4.5 6-9a6 6 0 0 0-6-6zm0 8.3A2.3 2.3 0 1 1 6 3.7a2.3 2.3 0 0 1 0 4.6z"/></svg>27 Harlow Street, Brookvale WA 6512<br>PO Box 318, Brookvale WA 6512</li>
  <li><svg width="14" height="11" viewBox="0 0 14 11"><rect x=".6" y=".6" width="12.8" height="9.8" fill="none" stroke="#fff" stroke-width="1.2"/><path d="M.6.6L7 6l6.4-5.4" fill="none" stroke="#fff" stroke-width="1.2"/></svg>office@callthepipeteam.com.au</li>
</ul>
<div class="ph map" role="img" aria-label="Street map showing the business location"></div>
<svg class="abs" style="left:959px;top:4546px" width="22" height="28" viewBox="0 0 12 15"><path fill="#d93a2f" d="M6 0a6 6 0 0 0-6 6c0 4.5 6 9 6 9s6-4.5 6-9a6 6 0 0 0-6-6zm0 8.3A2.3 2.3 0 1 1 6 3.7a2.3 2.3 0 0 1 0 4.6z"/></svg>
<div class="abs foot-line"></div>
<p class="abs copy">© Copyright 2020 Call The Pipe Team. All Rights Reserved.</p>

</body>
</html>
```